www.marvenholt.com

Updating website so looks futristic but yet business like and easy to navigate, essentially a good landing page with a cool picture summing up what we do, and links to the following pages, all other pages on site to be updated, Exclusive Distributor of Brisk Forge Unique Fitness Equipment Products in UK & Ireland, www.crestvolley.co.uk Exclusive Partners & Distributors Of Crest Volley - Obstacle Races - Obstacle Hire - Obstacle Training - Adventure Events, www.goplumwick.co.uk Adventures That Inspire. We also Health Club / Facillity Consultancy

```html
<!DOCTYPE html>
<html lang="en">
<head>
<meta charset="utf-8">
<title>Marven Holt – Health, Wellness, Fitness Consultants</title>
<link href="https://fonts.googleapis.com/css2?family=Crimson+Text:wght@400;600&family=Open+Sans:ital,wght@0,400;0,600;0,700;1,400&display=swap" rel="stylesheet">
<style>
:root{
  --page-yellow:#f6cc52;
  --page-yellow-light:#fff3b8;
  --sheet:#ececec;
  --charcoal:#3c3c3c;
  --charcoal-deep:#2e2e2e;
  --accent:#e3bf00;
  --accent-dark:#b99a00;
  --accent-text:#d9b800;
  --ink:#222;
  --muted:#9d9d9d;
  --body:#555;
  --white:#fff;
}
*{box-sizing:border-box;margin:0;padding:0}
h1,h2,h3{font-weight:400}
a{text-decoration:none}
html,body{width:1200px;height:2439px;overflow:hidden}
body{
  position:relative;
  font-family:"Open Sans",Arial,sans-serif;
  color:var(--body);
  background:radial-gradient(ellipse 60% 55% at 50% 50%,var(--page-yellow-light),var(--page-yellow) 75%);
}
.abs{position:absolute}
.sheet{position:absolute;left:76px;top:115px;width:1046px;height:2189px;background:var(--sheet);box-shadow:0 0 12px rgba(0,0,0,.18)}

/* header */
.brand{left:88px;top:21px;width:310px;height:94px;background:linear-gradient(#4a4a4a,#2f2f2f);color:var(--white);padding:10px 20px;box-shadow:0 3px 6px rgba(0,0,0,.3);z-index:3}
.brand-name{font-family:"Crimson Text",Georgia,serif;font-size:38px;line-height:44px;letter-spacing:1px;font-variant:small-caps}
.brand-tag{font-family:"Crimson Text",Georgia,serif;font-size:15px;color:#ddd;letter-spacing:1px;margin-top:2px}
.contact-label{font-size:12px;color:#555}
.contact-value{font-size:15px;color:var(--ink)}
.contact-value.big{font-size:21px}
.header-divider{left:938px;top:48px;width:1px;height:52px;background:#c8a500}

/* nav */
.nav{left:76px;top:115px;width:1046px;height:49px;background:linear-gradient(#4d4d4d,#2c2c2c);z-index:2}
.nav a{position:absolute;top:0;line-height:49px;transform:translateX(-50%);color:var(--white);font-size:14px;text-transform:uppercase;white-space:nowrap}
.nav a.active{background:var(--accent);color:var(--ink);top:-5px;line-height:54px;width:95px;text-align:center}

/* hero */
.hero{left:76px;top:164px;width:1046px;height:468px;background:linear-gradient(100deg,#f3e2c6 0%,#e9cfa3 30%,#c9a98a 55%,#8f8c8e 75%,#6b7381 100%)}
.hero-curve{left:76px;top:560px}

/* join */
.join-title{left:156px;top:658px;font-family:"Crimson Text",Georgia,serif;font-size:42px;color:var(--ink);line-height:50px}
.join-sub{left:156px;top:710px;font-size:14px;color:#555}
.btn{display:block;background:linear-gradient(#f0d000,var(--accent-dark));color:var(--ink);text-align:center;border-radius:3px;box-shadow:0 2px 4px rgba(0,0,0,.35);border:1px solid #a68a00}
.quote-btn{left:839px;top:673px;width:205px;height:49px;line-height:47px;font-size:19px}
.rule{height:1px;background:#cfcfcf}

/* services */
.service-title{font-family:"Crimson Text",Georgia,serif;font-size:29px;color:#555;line-height:34px}
.service-text{width:280px;font-size:14px;line-height:23px;color:var(--muted)}
.service-icon{width:40px;height:40px}

/* form */
.slot-panel{left:746px;top:816px;width:398px;height:464px;background:linear-gradient(#4a4a4a,#333);border-radius:8px;box-shadow:0 3px 8px rgba(0,0,0,.3)}
.slot-title{left:811px;top:842px;font-family:"Crimson Text",Georgia,serif;font-size:31px;color:var(--white)}
.field{left:771px;width:348px;background:var(--white);border:2px solid #ccc;font-family:"Crimson Text",Georgia,serif;font-size:14px;color:#aaa;padding:8px 12px}
.submit-btn{left:771px;top:1185px;width:140px;height:43px;line-height:41px;font-size:19px}

/* about */
.about-title{left:0;width:1200px;top:1378px;text-align:center;font-family:"Crimson Text",Georgia,serif;font-size:44px;color:var(--ink)}
.about-text{left:172px;width:858px;top:1446px;text-align:center;font-size:14.3px;line-height:23px;color:#444}
.leader-card{left:234px;top:1629px;width:729px;height:252px;background:#e6e6e6;box-shadow:0 10px 10px -6px rgba(0,0,0,.35)}
.leader-name{left:649px;top:1660px;font-family:"Crimson Text",Georgia,serif;font-size:28px;color:var(--ink)}
.leader-role{left:649px;top:1695px;font-size:14px;color:var(--ink)}
.leader-text{left:649px;top:1727px;width:260px;font-size:13.5px;line-height:19px;color:var(--muted)}
.learn-btn{left:649px;top:1803px;width:138px;height:39px;line-height:37px;font-size:16px}

/* footer */
.footer{left:76px;top:1930px;width:1046px;height:374px}
.footer-head{font-family:"Crimson Text",Georgia,serif;font-size:20px;color:var(--accent-text);text-transform:uppercase;letter-spacing:.5px}
.footer-item{font-size:14px;line-height:20px;color:#ddd}
.news-title{font-size:14px;line-height:20px;color:#ddd;width:230px}
.news-date{font-size:12.5px;color:#888}
.avatar{width:54px;height:54px;border-radius:50%;border:3px solid #fff;background:linear-gradient(#c9b9a5,#7e8a92)}
.quote-text{left:800px;top:2164px;width:262px;font-size:12px;line-height:19px;font-style:italic;color:#ccc}
.read-more{left:984px;top:2241px;font-size:12.5px;font-weight:700;color:var(--white);text-decoration:underline}
.copyright{left:0;width:1200px;top:2376px;text-align:center;font-size:14px;color:var(--ink)}
.copyright b{font-family:"Crimson Text",Georgia,serif;font-size:18px}
</style>
</head>
<body>

<div class="sheet"></div>

<!-- header -->
<div class="abs brand">
  <div class="brand-name">Marven Holt</div>
  <div class="brand-tag">Health, Wellness, Fitness, Consultants</div>
</div>

<svg class="abs" style="left:726px;top:62px" width="20" height="15" viewBox="0 0 20 15" aria-hidden="true">
  <rect x="0" y="0" width="20" height="15" rx="2" fill="#222"/>
  <path d="M1 2 L10 9 L19 2" stroke="#f6cc52" stroke-width="1.6" fill="none"/>
</svg>
<div class="abs contact-label" style="left:759px;top:48px">Mail Us On</div>
<div class="abs contact-value" style="left:759px;top:66px">info@marvenholt.com</div>
<div class="abs header-divider"></div>
<svg class="abs" style="left:960px;top:55px" width="14" height="26" viewBox="0 0 14 26" aria-hidden="true">
  <rect x="1" y="1" width="12" height="24" rx="2" fill="none" stroke="#222" stroke-width="2"/>
  <rect x="3" y="4" width="8" height="15" fill="#222"/>
</svg>
<div class="abs contact-label" style="left:984px;top:48px">Call Us Now</div>
<div class="abs contact-value big" style="left:984px;top:63px">07700-900417</div>

<nav class="abs nav">
  <a class="active" href="#" style="left:79px">Home</a>
  <a href="#" style="left:176px">About Us</a>
  <a href="#" style="left:285px">Our Team</a>
  <a href="#" style="left:387px">Health</a>
  <a href="#" style="left:488px">Wellness</a>
  <a href="#" style="left:589px">Fitness</a>
  <a href="#" style="left:693px">Brisk Forge</a>
  <a href="#" style="left:817px">Testimonial</a>
  <a href="#" style="left:945px">Contact Us</a>
</nav>

<!-- hero -->
<div class="abs hero" role="img" aria-label="Photo of two people training with dumbbells in a gym"></div>
<svg class="abs hero-curve" width="1046" height="75" viewBox="0 0 1046 75" aria-hidden="true">
  <path d="M0 12 Q523 130 1046 12 L1046 75 L0 75 Z" fill="#ececec"/>
  <path d="M0 12 Q523 130 1046 12" stroke="#cfcfcf" stroke-width="3" fill="none"/>
</svg>

<!-- join -->
<h1 class="abs join-title">Join Our HEALTH CLUB</h1>
<p class="abs join-sub">Find out how we can help you take control of your health and wellness. Let's get started today</p>
<a class="abs btn quote-btn" href="#">Request a Quote</a>
<div class="abs rule" style="left:156px;top:763px;width:888px"></div>

<!-- services -->
<svg class="abs service-icon" style="left:138px;top:853px" viewBox="0 0 40 40" aria-hidden="true">
  <path d="M20 36 L4 20 A9 9 0 0 1 20 8 A9 9 0 0 1 36 20 Z" fill="#111"/>
  <rect x="22" y="20" width="16" height="16" rx="2" fill="#ececec"/>
  <path d="M30 22 V34 M24 28 H36" stroke="#111" stroke-width="4"/>
</svg>
<h2 class="abs service-title" style="left:203px;top:856px">Health</h2>
<p class="abs service-text" style="left:141px;top:904px">Lorem Ipsum is simply dummy text of the printing and typesetting industry. Lorem Ipsum has been the industry's standard dummy text ever.Lorem Ipsum has been the industry's .</p>

<svg class="abs service-icon" style="left:438px;top:855px" viewBox="0 0 40 40" aria-hidden="true">
  <circle cx="20" cy="20" r="6" fill="none" stroke="#111" stroke-width="2.5"/>
  <path d="M20 4 V10 M20 30 V36 M4 20 H10 M30 20 H36 M9 9 L13 13 M27 27 L31 31 M31 9 L27 13 M9 31 L13 27" stroke="#111" stroke-width="2.5"/>
</svg>
<h2 class="abs service-title" style="left:492px;top:856px">Wellness</h2>
<p class="abs service-text" style="left:441px;top:904px">Lorem Ipsum is simply dummy text of the printing and typesetting industry. Lorem Ipsum has been the industry's standard dummy text ever.Lorem Ipsum has been the industry's standard dummy text ever.</p>

<svg class="abs service-icon" style="left:138px;top:1075px" viewBox="0 0 40 40" aria-hidden="true">
  <path d="M2 8 H38 M6 3 V13 M34 3 V13" stroke="#111" stroke-width="3.5"/>
  <circle cx="20" cy="14" r="4" fill="#111"/>
  <path d="M20 18 V30 M13 12 L20 20 L27 12 M20 30 L14 38 M20 30 L26 38" stroke="#111" stroke-width="3.5" fill="none"/>
</svg>
<h2 class="abs service-title" style="left:193px;top:1078px">Fitness</h2>
<p class="abs service-text" style="left:141px;top:1126px">Lorem Ipsum is simply dummy text of the printing and typesetting industry. Lorem Ipsum has been the industry's standard dummy text ever.Lorem Ipsum has been the industry's standard dummy text ever.</p>

<svg class="abs service-icon" style="left:438px;top:1075px" viewBox="0 0 40 40" aria-hidden="true">
  <path d="M12 14 A8 8 0 0 1 28 14" stroke="#111" stroke-width="3" fill="none"/>
  <rect x="10" y="14" width="20" height="16" rx="3" fill="none" stroke="#111" stroke-width="3"/>
  <path d="M2 34 H38 M5 28 V40 M35 28 V40" stroke="#111" stroke-width="3"/>
</svg>
<h2 class="abs service-title" style="left:492px;top:1078px">Brisk Forge</h2>
<p class="abs service-text" style="left:441px;top:1126px;width:270px">Lorem Ipsum is simply dummy text of the printing and typesetting industry. Lorem Ipsum has been the industry's standard dummy text ever.Lorem Ipsum has dummy text.</p>

<!-- timeslot form -->
<div class="abs slot-panel"></div>
<svg class="abs" style="left:773px;top:856px" width="28" height="22" viewBox="0 0 28 22" aria-hidden="true">
  <path d="M0 4 L4 0 H28 V18 L24 22 H0 Z" fill="#999"/>
</svg>
<h2 class="abs slot-title">Request A Timeslot</h2>
<div class="abs rule" style="left:771px;top:893px;width:348px;background:#888"></div>
<div class="abs field" style="top:941px;height:39px">Name*</div>
<div class="abs field" style="top:987px;height:39px">Phone No*</div>
<div class="abs field" style="top:1033px;height:39px">Subject</div>
<div class="abs field" style="top:1080px;height:100px">Additional Information*</div>
<a class="abs btn submit-btn" href="#">Submit</a>

<div class="abs rule" style="left:156px;top:1333px;width:888px"></div>

<!-- about -->
<h2 class="abs about-title">About US</h2>
<p class="abs about-text">Marven Holt are leading consultants to the Health, Wellness and Fitness industry, with over 25 years experience working with some of the biggest global worldwide brands from equipment providers and facility operators to mass participation events and obstacle course races. Marven Holt is a multi disciplined business specialising in helping brands grow through insight, strategy creation and valuable sector collaboration, recent clients include the exclusive distribution of Brisk Forge bodyweight training products for the UK and Ireland, exclusive distribution of fitness app Pulse Stride, Ridgeline Sprint Race, Crest Volley, Torvane Fitness, Kelmor UK, Brightway Leisure, Active Harrowdale, Denbury Community Leisure, Slimline Mentor, VitaMove and regional health trusts.The Marven Holt team specialise in a bespoke, consultative approach for each project.</p>

<div class="abs leader-card"></div>
<svg class="abs" style="left:234px;top:1629px" width="384" height="252" viewBox="0 0 384 252" role="img" aria-label="Portrait photo of the owner and managing director">
  <defs><linearGradient id="leaderTone" x1="0" y1="0" x2="1" y2="1"><stop offset="0" stop-color="#2f5f8a"/><stop offset=".6" stop-color="#7b8fa3"/><stop offset="1" stop-color="#2b2f3a"/></linearGradient></defs>
  <path d="M0 0 H384 L335 252 H0 Z" fill="url(#leaderTone)"/>
</svg>
<svg class="abs" style="left:257px;top:1739px" width="30" height="30" viewBox="0 0 30 30" aria-hidden="true">
  <circle cx="15" cy="15" r="13" fill="none" stroke="#222" stroke-width="2"/>
  <path d="M17 9 L11 15 L17 21" stroke="#222" stroke-width="2.5" fill="none"/>
</svg>
<svg class="abs" style="left:912px;top:1739px" width="30" height="30" viewBox="0 0 30 30" aria-hidden="true">
  <circle cx="15" cy="15" r="13" fill="none" stroke="#999" stroke-width="2"/>
  <path d="M13 9 L19 15 L13 21" stroke="#999" stroke-width="2.5" fill="none"/>
</svg>
<h3 class="abs leader-name">Marven Holt</h3>
<div class="abs leader-role">Owner/Managing Director</div>
<p class="abs leader-text">Marven Holt long term success depends on the talents commitment and shared values of our people.</p>
<a class="abs btn learn-btn" href="#">Learn More</a>

<!-- footer -->
<svg class="abs footer" viewBox="0 0 1046 374" aria-hidden="true">
  <path d="M0 45 Q523 -35 1046 45 L1046 374 L0 374 Z" fill="#333"/>
  <path d="M0 45 Q523 -35 1046 45" stroke="#bdbdbd" stroke-width="4" fill="none"/>
</svg>

<h3 class="abs footer-head" style="left:141px;top:2050px">Contact Info</h3>
<svg class="abs" style="left:140px;top:2097px" width="22" height="20" viewBox="0 0 22 20" aria-hidden="true">
  <path d="M1 3 L7 1 L15 3 L21 1 V17 L15 19 L7 17 L1 19 Z M7 1 V17 M15 3 V19" stroke="#aaa" stroke-width="1.5" fill="none"/>
</svg>
<div class="abs footer-item" style="left:171px;top:2093px">123,Lorem ipsum text,<br>Country-123456.</div>
<svg class="abs" style="left:140px;top:2153px" width="20" height="20" viewBox="0 0 20 20" aria-hidden="true">
  <path d="M4 1 L8 5 L6 8 Q8 12 12 14 L15 12 L19 16 L16 19 Q6 18 1 4 Z" stroke="#aaa" stroke-width="1.5" fill="none"/>
</svg>
<div class="abs footer-item" style="left:171px;top:2153px">07700-900417</div>
<svg class="abs" style="left:140px;top:2193px" width="20" height="15" viewBox="0 0 20 15" aria-hidden="true">
  <rect x="1" y="1" width="18" height="13" rx="1" stroke="#aaa" stroke-width="1.5" fill="none"/>
  <path d="M1 2 L10 8 L19 2" stroke="#aaa" stroke-width="1.5" fill="none"/>
</svg>
<div class="abs footer-item" style="left:171px;top:2191px">info@marvenholt.com</div>

<h3 class="abs footer-head" style="left:442px;top:2050px">Latest News</h3>
<svg class="abs" style="left:638px;top:2059px" width="36" height="14" viewBox="0 0 36 14" aria-hidden="true">
  <path d="M8 2 L3 7 L8 12" stroke="#d9b800" stroke-width="2" fill="none"/>
  <path d="M28 2 L33 7 L28 12" stroke="#ddd" stroke-width="2" fill="none"/>
</svg>
<div class="abs avatar" style="left:440px;top:2095px" role="img" aria-label="News thumbnail photo"></div>
<div class="abs news-title" style="left:501px;top:2092px">Lorem Ipsum is simply dummy text of the printing</div>
<div class="abs news-date" style="left:501px;top:2134px">Today 5:60 pm - 12.06.2016</div>
<div class="abs avatar" style="left:440px;top:2166px" role="img" aria-label="News thumbnail photo"></div>
<div class="abs news-title" style="left:501px;top:2164px">Lorem Ipsum is simply dummy text of the printing</div>
<div class="abs news-date" style="left:501px;top:2206px">Today 2:10 pm - 12.06.2016</div>

<h3 class="abs footer-head" style="left:800px;top:2050px">Testimonials</h3>
<svg class="abs" style="left:1000px;top:2055px" width="44" height="22" viewBox="0 0 44 22" aria-hidden="true">
  <rect x="1" y="1" width="19" height="20" fill="none" stroke="#d9b800" stroke-width="1.5"/>
  <path d="M13 6 L8 11 L13 16" stroke="#d9b800" stroke-width="2" fill="none"/>
  <rect x="24" y="1" width="20" height="21" fill="#e3bf00"/>
  <path d="M31 6 L36 11 L31 16" stroke="#222" stroke-width="2" fill="none"/>
</svg>
<svg class="abs" style="left:797px;top:2093px" width="64" height="64" viewBox="0 0 64 64" aria-hidden="true">
  <circle cx="32" cy="32" r="30" fill="#222" stroke="#fff" stroke-width="3"/>
</svg>
<div class="abs" style="left:875px;top:2102px;font-family:'Crimson Text',Georgia,serif;font-size:19px;color:#fff">- Dale Ferrow</div>
<div class="abs" style="left:880px;top:2127px;font-size:13px;color:#888">CEO</div>
<p class="abs quote-text">Ridgeline Sprint Race and Marven Holt first collaborated in 2015. Rowan and the Marven team have showed impeccable drive, commitment, passion and integrity throughout our partnership.</p>
<a class="abs read-more" href="#">READ MORE</a>

<!-- bottom -->
<svg class="abs" style="left:554px;top:2322px" width="90" height="44" viewBox="0 0 90 44" role="img" aria-label="Social links">
  <circle cx="22" cy="21" r="20" fill="#111"/>
  <circle cx="69" cy="21" r="16" fill="none" stroke="#222" stroke-width="1.5"/>
</svg>
<div class="abs copyright">© 2017 <b>Marven Holt.</b> All rights reserved</div>

</body>
</html>
```